CREATE A BUSINESS CARD FOR A BOAT CLEANING SERVICE

WE ARE STARTING A NEW BOAT CLEANING BUSINESS. WE DIVE UNDERWATER TO CLEAN BOAT HULLS, JETTIES, UNDERWATER STRUCTURES ETC. WE ARE LOOKING FOR AN UPPERMARKET MODERN LOGO AND BUSINESS CARD AS ALOT OF OUR TARGET MARKET WILL BE HIGH END. YOU HAVE TO DESIGN A BUSINESS CARD AND LOGO SEPERATELY .
THE BUSINESS CARD DIMESNION MUST BE STANDARD SIZE.
The standard dimensions of a printed business card are 3.5 x 2 inches

Target Market(s)

UNDERWATER SERVICED

Industry/Entity Type

Business

Contact Information for Business Card

HOLLAND UNDERWATER SERVICES

Font styles to use
Serif

Colors

Designer to choose colors to be used in the design.

Requirements
Must have
• HOLLAND
Nice to have
• dark
Should not have
• more than 3 colors

```html
<!DOCTYPE html>
<html lang="en">
<head>
<meta charset="utf-8">
<title>Holland Underwater Services – Business Card</title>
<link rel="stylesheet" href="https://fonts.googleapis.com/css2?family=Lato:wght@400;700&display=swap">
<style>
  :root {
    --stage: #1f1f1f;
    --navy: #174f8c;
    --navy-light: #1b5798;
    --white: #ffffff;
    --ink-blue: #1a4f8e;
    --ink-grey: #6b6b6b;
    --card-text: #f2f5fa;
  }
  html, body {
    margin: 0;
    padding: 0;
    width: 1200px;
    height: 900px;
    overflow: hidden;
    background: var(--stage);
    font-family: "Lato", sans-serif;
  }
  .stage {
    position: relative;
    width: 1200px;
    height: 900px;
  }
  .card {
    position: absolute;
    top: 306px;
    width: 439px;
    height: 271px;
    border-radius: 10px;
    box-sizing: border-box;
  }
  .card-front {
    left: 149px;
    background: linear-gradient(160deg, var(--navy-light), var(--navy));
    color: var(--card-text);
  }
  .card-back {
    left: 609px;
    background: var(--white);
  }
  .brand {
    position: absolute;
    left: 22px;
    top: 39px;
    font-weight: 700;
    color: var(--card-text);
    line-height: 1;
  }
  .brand-name {
    display: block;
    font-size: 48px;
    letter-spacing: 0;
  }
  .brand-tag {
    display: block;
    font-size: 12.5px;
    letter-spacing: 2.3px;
    margin-top: 1px;
    padding-left: 5px;
  }
  .person {
    position: absolute;
    left: 24px;
    top: 154px;
  }
  .person-name {
    font-size: 16px;
    font-weight: 700;
    margin: 0;
    line-height: 18px;
  }
  .person-role {
    font-size: 13px;
    margin: 0;
    line-height: 16px;
  }
  .contact-list {
    position: absolute;
    left: 24px;
    top: 197px;
    margin: 0;
    padding: 0;
    list-style: none;
    font-size: 13px;
    line-height: 16px;
  }
  .contact-list li {
    display: flex;
    align-items: center;
    gap: 4px;
  }
  .contact-list svg {
    width: 10px;
    height: 10px;
    fill: var(--card-text);
  }
  .address {
    position: absolute;
    right: 28px;
    top: 213px;
    font-size: 13px;
    line-height: 16px;
    text-align: right;
    font-style: normal;
  }
  .back-brand {
    position: absolute;
    left: 0;
    right: 0;
    top: 151px;
    text-align: center;
    font-weight: 700;
    color: var(--ink-blue);
    line-height: 1;
  }
  .back-brand .brand-name {
    font-size: 52px;
  }
  .back-brand .brand-tag {
    font-size: 13px;
    letter-spacing: 2.6px;
    margin-top: 0;
    padding-left: 0;
    color: var(--ink-grey);
  }
</style>
</head>
<body>
<main class="stage">
  <section class="card card-front" aria-label="Business card front">
    <div class="brand">
      <span class="brand-name">HOLLAND</span>
      <span class="brand-tag">UNDERWATER SERVICES</span>
    </div>
    <div class="person">
      <p class="person-name">MARCUS DELANEY</p>
      <p class="person-role">Managing Director</p>
    </div>
    <ul class="contact-list">
      <li>
        <svg viewBox="0 0 10 10" aria-hidden="true"><path d="M1 3c0-1 1-2 2-2h4c1 0 2 1 2 2v1H7V3H3v1H1z M2 5h6l1 4H1z"/></svg>
        444 555 7290
      </li>
      <li>
        <svg viewBox="0 0 10 10" aria-hidden="true"><path d="M1 2h8v6H1z M1 2l4 3 4-3" stroke="#174f8c" stroke-width="0.8"/></svg>
        info@hollanddive.com
      </li>
      <li>
        <svg viewBox="0 0 10 10" aria-hidden="true"><circle cx="5" cy="5" r="4.5"/><path d="M1 5h8M5 0.5c-2 2-2 7 0 9M5 0.5c2 2 2 7 0 9" stroke="#174f8c" stroke-width="0.7" fill="none"/></svg>
        www.hollanddive.com
      </li>
    </ul>
    <address class="address">318, Harbour Quay Road<br>Marina Bay,60718</address>
  </section>

  <section class="card card-back" aria-label="Business card back">
    <div class="back-brand">
      <span class="brand-name">HOLLAND</span>
      <span class="brand-tag">UNDERWATER SERVICES</span>
    </div>
  </section>
</main>
</body>
</html>
```